Larkmoor Drones Business Card

We are a new company based in Central Queensland, Australia that uses specalised drones (Voskel Ferra Q80) to undertake mainly agricultural operations, like spraying weeds, spraying crops, spreading seed etc. I have attached a Plimbo proof of a card I was thinking along the lines of - purely a start point. The drone used in the business card MUST be a Voskel Ferra Q80.
I am very open to other ideas, especially fonts and layout. I don't have website etc set up yet.
The images are stock and easily interchangeable, I just ask that any background images reflect the local central Queensland area. The photo of the drone is not even complete (propellers cut off) and I need a new stock photo – I’m not sure if this is an issue, or I can pay for an image if need be. PLEASE FIND AN FERRA Q80 image - 4 sprayers, not 6.
The logo/business name is very draft and looking for further ideas, ideally incorporating drones or agriculture design elements into the design of the business name. The business name needs work on the graphic/design – it is a draft that I have included, the drone propellers (being a different colour) are DRAFT only and intended for changes. PLEASE DO NOT USE THE DRONE PORPELLER I HAVE USED AS A DRAFT. TRY TO FIND SOMETHING ELSE.. The arrow is a shape and not aligned in any way, I would also like ideas on different fonts and additional elements, like air streams, aviation elements, aviation or country western (farming like) themes and fonts etc.
Ideally looking at staying within the blue, green and yellow colours, keeping with an natural, outdoorsy, environmental feel.

Target Market(s)

Farmers, Agriculture, Local Governments, Land Managers

Industry/Entity Type

Agriculture, Drones, Aviation

Contact Information for Business Card

Agricultural Drone (Voskel Ferra Q80), Farming, Business Name.

Font styles to use
Sans Serif

Colors
0054AA
0677BA
7BADD7
CADEEF
E8F1F8
0094D4
00A9DD
6FCCEA
C7EBF8
E9F6FB
00AB8E
00BBA5
67D7C9
C6EFE9
E9F9F6
59FF00
82FF00
B8FF75
E3FFCB
F4FFEA

Requirements
Must have
• Voskel Ferra Q80 Drone
Should not have
• Tractors

```html
<!DOCTYPE html>
<html lang="en">
<head>
<meta charset="utf-8">
<title>Larkmoor Drones Business Card</title>
<link rel="stylesheet" href="https://fonts.googleapis.com/css2?family=Saira:wght@400;500;800&family=Montserrat:wght@500&display=swap">
<style>
  :root {
    --stage: #262626;
    --navy: #1c3f92;
    --band: #37497f;
    --ink: #2d3138;
    --white: #ffffff;
    --sky-top: #c9964a;
    --sky-mid: #f0c466;
    --sky-low: #f6d790;
    --hills: #6f8a6a;
    --field-far: #a9b537;
    --field-near: #6f8b1e;
    --panel: rgba(226, 236, 200, 0.55);
    --drone-dark: #34373b;
    --drone-mid: #6b6f75;
    --drone-light: #d9dbde;
  }
  * { box-sizing: border-box; margin: 0; padding: 0; }
  html, body { width: 1200px; height: 1059px; overflow: hidden; background: var(--stage); }
  .canvas { position: relative; width: 1200px; height: 1059px; }

  .card {
    position: absolute; left: 257px; width: 691px; height: 395px;
    border-radius: 24px; overflow: hidden;
  }
  .card--front { top: 90px; }
  .card--back { top: 547px; }

  .landscape {
    position: absolute; inset: 0;
    background: linear-gradient(180deg, var(--sky-top) 0%, var(--sky-mid) 22%, var(--sky-low) 38%, var(--hills) 44%, var(--field-far) 48%, var(--field-far) 70%, var(--field-near) 100%);
  }

  .brand { position: absolute; left: 0; right: 0; text-align: center; }
  .brand__name {
    font-family: "Saira", sans-serif; font-weight: 800; text-transform: uppercase;
    font-size: 50px; line-height: 1; letter-spacing: 0.5px; color: var(--navy);
  }
  .brand__tagline {
    font-family: "Montserrat", sans-serif; font-weight: 500; font-size: 16px;
    letter-spacing: 2.6px; color: var(--ink); margin-top: 8px;
  }
  .card--front .brand { top: 50px; }

  .contact-panel {
    position: absolute; left: 40px; top: 173px; width: 612px; height: 181px;
    background: var(--panel);
  }
  .contact-list { position: absolute; left: 70px; top: 26px; list-style: none; }
  .contact-list li, .social-list li {
    display: flex; align-items: center; gap: 6px; height: 27px;
    font-family: "Saira", sans-serif; font-size: 17px; color: var(--ink);
  }
  .contact-list li:first-child { font-size: 18px; }
  .contact-list .icon, .social-list .icon { width: 22px; height: 22px; flex: none; }
  .social-list { position: absolute; left: 384px; top: 17px; list-style: none; }
  .social-list li { height: 37px; gap: 12px; }

  .licence {
    position: absolute; left: 0; right: 0; top: 129px; text-align: center;
    font-family: "Saira", sans-serif; font-size: 14.5px; line-height: 17px; color: var(--ink);
  }

  .services {
    position: absolute; left: 0; right: 0; top: 28px; text-align: center;
    font-family: "Saira", sans-serif; font-weight: 800; font-size: 36px; line-height: 1;
    color: var(--navy); word-spacing: 8px;
  }
  .drone-photo {
    position: absolute; left: 166px; top: 94px; width: 344px; height: 144px;
    border-radius: 10px;
    background: linear-gradient(180deg, var(--drone-light) 0%, var(--drone-mid) 35%, var(--drone-dark) 100%);
  }
  .brand-band {
    position: absolute; left: 0; right: 0; top: 263px; height: 90px; background: var(--band);
  }
  .card--back .brand { top: 15px; }
  .card--back .brand__name { color: var(--white); font-size: 48px; }
  .card--back .brand__tagline { color: var(--white); margin-top: 6px; }
</style>
</head>
<body>
<main class="canvas">

  <section class="card card--front">
    <div class="landscape" role="img" aria-label="Golden sunset sky over hills and a green crop field"></div>
    <div class="brand">
      <div class="brand__name">Larkmoor Drones</div>
      <div class="brand__tagline">SERVICING CENTRAL QUEENSLAND</div>
    </div>
    <div class="contact-panel">
      <ul class="contact-list">
        <li>
          <svg class="icon" viewBox="0 0 22 22"><circle cx="11" cy="11" r="11" fill="#1c3f92"/><path d="M7.5 6.5c.6-.6 1.4-.5 1.8.1l.9 1.4c.3.5.2 1.1-.2 1.4l-.6.5c.6 1.3 1.5 2.2 2.8 2.8l.5-.6c.4-.4 1-.5 1.4-.2l1.4.9c.6.4.7 1.2.1 1.8-.8.9-2 1.2-3.2.7-2.2-1-3.9-2.7-4.9-4.9-.5-1.2-.2-2.4.7-3.2z" fill="#fff"/></svg>
          123 456 7890
        </li>
        <li>
          <svg class="icon" viewBox="0 0 22 22"><circle cx="11" cy="11" r="11" fill="#1c3f92"/><rect x="5.5" y="7.5" width="11" height="7.5" rx="1" fill="#fff"/><path d="M5.8 8l5.2 4 5.2-4" fill="none" stroke="#1c3f92" stroke-width="1.2"/></svg>
          larkmoordrone@fieldpost.com
        </li>
        <li>
          <svg class="icon" viewBox="0 0 22 22"><circle cx="11" cy="11" r="11" fill="#1c3f92"/><circle cx="11" cy="11" r="6" fill="none" stroke="#fff" stroke-width="1.4"/><path d="M5 11h12M11 5c-2.5 3-2.5 9 0 12M11 5c2.5 3 2.5 9 0 12" fill="none" stroke="#fff" stroke-width="1.1"/></svg>
          www.website.com
        </li>
      </ul>
      <ul class="social-list">
        <li><svg class="icon" viewBox="0 0 22 22"><circle cx="11" cy="11" r="11" fill="#1c3f92"/></svg>@larkmoordrone</li>
        <li><svg class="icon" viewBox="0 0 22 22"><rect x="1" y="1" width="20" height="20" rx="5" fill="#1c3f92"/></svg>@larkmoordrone</li>
      </ul>
      <p class="licence">Fully Licensed and insured<br>RePL 1039572; ReOC 8841; PCR A317206</p>
    </div>
  </section>

  <section class="card card--back">
    <div class="landscape" role="img" aria-label="Golden sunset sky over hills and a green crop field"></div>
    <h2 class="services">SPRAY • WEED • SEED • FEED</h2>
    <div class="drone-photo" role="img" aria-label="Photo of a Voskel Ferra Q80 agricultural spray drone with four rotor arms hovering over the field"></div>
    <div class="brand-band">
      <div class="brand">
        <div class="brand__name">Larkmoor Drones</div>
        <div class="brand__tagline">SERVICING CENTRAL QUEENSLAND</div>
      </div>
    </div>
  </section>

</main>
</body>
</html>
```